CopperWanderer Stretching and Strength

We need a application design for a our first IOS application. the goal of the application is to categorize stretching and strength routines for triathlon.

We would like to see designs that use the color orange.

The design of the application should be compliant with the last version of the IOS Mobile.

For this first design we need the folowing pages:

1- Sign up
2- Log in
3- Home
4- View Exercises
5- Do it
6- Profile

The description of each page is in the attached document.

We need a logo design for the application. The logo should express that mission of the application that is for stretch and strength training for Triathlon.

We will use https://pellavokit.example to develop the application, if you have any experience of the limitation that this technology have it will be a plus.

If you have any question please feel free to contact us.

Reason: We will extend the deadline to be sure that we select the best design from all of you. we will take the final decision next Tuesday.

Target Market(s)

The market for my aplicación is the Running a Triathlon world.

Logo Text

CopperWanderer

Font styles to use
Serif

Colors
f37122
ffffff
dcdcdc

Requirements
Must have
• In some future we will add more features in the menu. We should considere it for the design.
• The designs should include all the screens in the power point.

```html
<!DOCTYPE html>
<html lang="en">
<head>
<meta charset="utf-8">
<title>Triathlon – Launch Screen</title>
<link rel="stylesheet" href="https://fonts.googleapis.com/css2?family=Roboto:wght@400;500&display=swap">
<style>
  :root {
    --brand-orange: #f07232;
    --ink-white: #ffffff;
    --soft-grey: #dcdcdc;
    --backdrop: #d6e3ef;
  }
  * { margin: 0; padding: 0; box-sizing: border-box; }
  html, body {
    width: 1200px;
    height: 1200px;
    overflow: hidden;
    background: var(--backdrop);
    font-family: "Roboto", Arial, sans-serif;
  }
  .canvas {
    width: 1200px;
    height: 1200px;
    display: flex;
    align-items: center;
    justify-content: center;
  }
  .screen {
    position: relative;
    width: 617px;
    height: 1100px;
    background: var(--brand-orange);
    color: var(--ink-white);
    overflow: hidden;
  }
  .status-bar {
    position: absolute;
    top: 10px;
    left: 10px;
    right: 10px;
    height: 24px;
    display: flex;
    align-items: center;
    justify-content: space-between;
    font-size: 18px;
    letter-spacing: 0.2px;
  }
  .status-left, .status-right {
    display: flex;
    align-items: center;
    gap: 7px;
    width: 200px;
  }
  .status-right { justify-content: flex-end; }
  .status-time { flex: 1; text-align: center; }
  .brand-mark {
    position: absolute;
    top: 312px;
    left: 50%;
    width: 110px;
    height: 110px;
    margin-left: -55px;
    border-radius: 50%;
    background: var(--ink-white);
  }
  .brand-name {
    position: absolute;
    top: 491px;
    left: 0;
    right: 0;
    text-align: center;
    font-size: 40px;
    font-weight: 500;
    letter-spacing: 0.4px;
    line-height: 1;
  }
  .brand-tagline {
    position: absolute;
    top: 540px;
    left: 0;
    right: 0;
    text-align: center;
    font-size: 20px;
    font-weight: 400;
    line-height: 1.2;
  }
  .footer-message {
    position: absolute;
    top: 962px;
    left: 0;
    right: 0;
    text-align: center;
    font-size: 26px;
    line-height: 1.2;
  }
  .app-version {
    position: absolute;
    top: 1040px;
    left: 0;
    right: 0;
    text-align: center;
    font-size: 19px;
    line-height: 1.2;
  }
</style>
</head>
<body>
  <main class="canvas">
    <section class="screen">
      <header class="status-bar">
        <div class="status-left">
          <svg class="signal-dots" width="52" height="12" viewBox="0 0 52 12" aria-hidden="true">
            <circle cx="5" cy="6" r="4.5" fill="#fff"/>
            <circle cx="15.5" cy="6" r="4.5" fill="#fff"/>
            <circle cx="26" cy="6" r="4.5" fill="#fff"/>
            <circle cx="36.5" cy="6" r="4" fill="none" stroke="#fff" stroke-width="1"/>
            <circle cx="47" cy="6" r="4" fill="none" stroke="#fff" stroke-width="1"/>
          </svg>
          <span class="carrier">LUMA</span>
          <svg class="wifi-icon" width="18" height="14" viewBox="0 0 18 14" aria-hidden="true">
            <path d="M1 5 A11 11 0 0 1 17 5" fill="none" stroke="#fff" stroke-width="2"/>
            <path d="M4 8 A7 7 0 0 1 14 8" fill="none" stroke="#fff" stroke-width="2"/>
            <path d="M9 13 L6.5 10.5 A3.5 3.5 0 0 1 11.5 10.5 Z" fill="#fff"/>
          </svg>
        </div>
        <div class="status-time">4:21 PM</div>
        <div class="status-right">
          <svg class="bluetooth-icon" width="12" height="18" viewBox="0 0 12 18" aria-hidden="true" opacity="0.7">
            <path d="M2 5 L10 12 L6 16 V2 L10 6 L2 13" fill="none" stroke="#fff" stroke-width="1.4"/>
          </svg>
          <span class="battery-level">100%</span>
          <svg class="battery-icon" width="38" height="16" viewBox="0 0 38 16" aria-hidden="true">
            <rect x="0.5" y="0.5" width="34" height="15" rx="3" fill="none" stroke="#fff"/>
            <rect x="2.5" y="2.5" width="30" height="11" rx="1.5" fill="#fff"/>
            <rect x="35.5" y="5" width="2" height="6" rx="1" fill="#fff"/>
          </svg>
        </div>
      </header>

      <div class="brand-mark" aria-hidden="true"></div>
      <h1 class="brand-name">TRIATHLON</h1>
      <p class="brand-tagline">Stretch and strength training for Triathlon</p>

      <p class="footer-message">Lorem ipsum dolor sit amet</p>
      <p class="app-version">v 0.0.2</p>
    </section>
  </main>
</body>
</html>
```